EXCITING DECK for Automotive dealers that shows how our Technology works.

General Concept
The deck should visually represent the Trade and Credit Lead Life Cycle program is a dynamic, interconnected journey, illustrating how leads are generated, nurtured, and converted. The focus should be on how your system flows seamlessly between credit and trade-in opportunities for consumers, with the goal of maximizing engagement and conversions.
Slide 1: Title Slide - Lead Life Cycle Program
• Visual Concept: A stylized cycle or wheel that represents the stages of the lead life cycle, with arrows connecting each stage.
• Headline: "Lead Life Cycle Program"
• Subhead line: "Credit Pre-Qualification and Trade-In Appraisal"
• Imagery: Modern, sleek graphics of vehicles, smartphones (for texting), email icons, and dollar signs for value.
Slide 2: Lead Generation Sources
• Visual Concept: A funnel with the top representing the different lead generation sources.
• Content:
o Top of Funnel (Leads Enter):
 Pre-Qualification Tool (Fast4Loan)- How it Works
 1. Converts Web Traffic into the highest quality lead on the market
 Vorqel Email/Mail Marketing – How it Works
 1. Delivers actionable leads from email marketing not Just OPENS AND CLICKS. Show the text demo. Audiences below
1. Past Sold Customers (Equity Targets)
2. Past Service Onlu Department Customers (Conquest Sales)
3. Unsold Leads (from previous interactions)
o Each source should have a distinct icon to represent it (e.g., envelope for email, a wrench for past service customers, etc.).
• Headline: "Multiple Lead Sources Feeding into the Program"
• Imagery: The funnel narrowing toward the next step with leads symbolized by icons flowing downward.
Slide 3: Credit Leads - Pre-Qualified Flow
• Visual Concept: A customer engaging with the Fast4Loan tool on their mobile, being pre-qualified, and then us sending a offer to appraise their trade.
• Flow Explanation:
o Customer pre-qualifies via Fast4Loan → Receives credit approval → Email and Mail Example to check trade-in value.
• Headline: "Pre-Qualified Leads: Offering Trade-In Appraisal"
• Imagery: A sequence that shows how a customer moves from pre-qualification to considering their trade-in value. To purchasing
Slide 4: Trade-In Leads - Valuation Flow
• Visual Concept: A customer who has received a trade-in valuation offer now being prompted to pre-qualify for financing.
• Flow Explanation:
o Customer texts for vehicle value → Receives trade-in appraisal → Offer to pre-qualify for financing appears link is at the bottom of the text response.
• Headline: "Trade-In Leads: Offering Credit Pre-Qualification"
• Imagery: A customer looking at their trade-in value on their phone and being shown an additional prompt to pre-qualify for a loan.
Slide 5: Cross-Offer Opportunities
• Visual Concept: A two-way street or cycle, illustrating the seamless transition between offering pre-qualification to trade-in customers and offering trade-in value to credit leads.
• Content:
o Two pathways:
1. Start as a Credit Lead → Offer Trade-In Valuation
2. Start as a Trade-In Lead → Offer Credit Pre-Qualification
o Headline: "Cross-Offer Opportunities for Maximum Engagement"
• Imagery: Arrows going in both directions, symbolizing the back-and-forth opportunities between credit and trade leads.
Digital Retargeting for Cross-Action Engagement
• Visual Concept: An omnichannel approach with a customer in the center, surrounded by email/Mail icons, Chatterbook, and Snapgrove logos. Arrows leading from each platform back to the customer, showing how these channels drive engagement.
• Content:
o Title: "Engage to Convert one lead type to get both with Email/Mail and Digital Retargeting"
o Explanation:
 Whether a lead starts as a Pre-Qualified Credit Lead or a Trade-In Valuation Lead, we use personalized Email/Mail Campaigns and Digital Retargeting Ads (Chatterbook & Snapgrove) to encourage them to take the next action.
 If they pre-qualify for credit, we retarget them with trade-in valuation offers.
 If they start with a trade-in valuation, we follow up with financing offers.
o Headline: "Leverage Email & Social Retargeting to Drive Cross-Action"
• Visuals:
o Icons of Email, Chatterbook, and Snapgrove: Showing the platforms through which you retarget leads.
o Customer Journey Map: Illustrating how leads who interacted once are guided to the next step (credit lead → trade-in offer, trade-in lead → pre-qualification).
o Arrows Flowing Between Channels: Showing how no matter where a lead starts, they are continually engaged through digital touchpoints until they complete both actions.
o Ad examples
• Call to Action: "Stay Top of Mind and Convert Leads into Multi-Action Customers"
This slide emphasizes how you’re leveraging both email/mail marketing and social media retargeting to move leads further along the customer journey, regardless of how they entered your funnel. The visuals should reinforce the idea of continuous engagement and omnipresent reminders for them to take action.
________________________________________
Slide 6: Lifecycle Representation
• Visual Concept: A circular diagram showing how leads can continuously move between credit and trade offers throughout their lifecycle.
• Content:
o Show how the lifecycle doesn’t end after one interaction, but can continue with follow-up offers.
o Headline: "Continuous Engagement Throughout the Lead Life Cycle"
• Imagery: Circular arrows or flowchart representing each stage looping back into the lifecycle, emphasizing that leads can be re-engaged.
Slide 7: Lead Conversion Goals
• Visual Concept: A progression from leads to successful transactions (e.g., a customer with keys to a new car). Showing that getting customers to take both of these actions delives a lead that is very committed to the process of buying.
• Content:
o End goal: Convert both credit and trade leads into sales.
o Show statistics or success metrics as optional data points.
o Headline: "Converting Leads into Sales"
• Imagery: A car dealership handing over keys, happy customers, and sold vehicles.
Slide 8: Next Steps / Call to Action
• Visual Concept: A final slide summarizing the key takeaways and next steps.
• Headline: "Maximize Lead Potential with Cross-Offer Opportunities"
• Imagery: A mix of credit leads, trade leads, and successful customer outcomes.
________________________________________These slides should be clean and modern, using simple but impactful visuals like arrows, icons, and flow diagrams to represent the journey. The key is to emphasize flow and interaction between credit and trade-in opportunities, showing the two-way cross-sell nature of your Lead Life Cycle Program.

I have attached a current deck so you can pull some basic product info and graphics into the new deck (PLEASE DONT JUST COPY THE OLD DECK). I have also included some of our email artwrok if you need it. If you want to look at our website go here www.plorvenadsgroup.example

Target Market(s)

Car Dealers

Industry/Entity Type

Automotive Marketing

Requirements
Must have
• PLEASE READ THE PROJECT DESCRIPTION
Nice to have
Should not have
• PLEASE dont just copy the deck i uploaded. I am looking for a differnt take.

```html
<!DOCTYPE html>
<html lang="en">
<head>
<meta charset="utf-8">
<title>Lead Life Cycle Program – Deck Overview</title>
<link href="https://fonts.googleapis.com/css2?family=Aldrich&family=Roboto:wght@400;500;700&display=swap" rel="stylesheet">
<style>
  :root{
    --board:#6f6f72;
    --paper:#ffffff;
    --paper-tint:#f4f4f4;
    --ink:#2e2e30;
    --ink-soft:#4a4a4d;
    --grey:#8a8a8c;
    --grey-light:#d9d9db;
    --red:#e31b2f;
    --red-dark:#c8142a;
    --teal:#5fd6cc;
    --purple:#6b4a9a;
    --blush:#e8d8de;
    --photo-warm:#c9b8a6;
    --photo-cool:#9fb4c6;
  }
  *{box-sizing:border-box;margin:0;padding:0}
  html,body{width:1200px;height:1116px;overflow:hidden;background:var(--board)}
  body{position:relative;font-family:"Roboto",sans-serif;color:var(--ink)}

  .slide{position:absolute;width:507px;height:285px;background:linear-gradient(160deg,var(--paper) 0%,var(--paper-tint) 100%);overflow:hidden;box-shadow:0 10px 22px rgba(0,0,0,.35)}
  .slide > *{position:absolute}
  .slide .graphics{left:0;top:0;width:507px;height:285px}

  .title{font-family:"Aldrich",sans-serif;font-size:18px;line-height:1;letter-spacing:.2px;text-transform:uppercase;color:var(--ink);white-space:nowrap;font-weight:400}
  .title .accent{color:var(--red)}
  .subtitle{font-size:10.5px;color:var(--ink-soft);white-space:nowrap}
  .page-no{right:11px;bottom:8px;font-size:5.5px;color:var(--ink)}

  .brand{display:flex;align-items:center;gap:4px;font-family:"Roboto",sans-serif;font-weight:700;color:var(--ink);letter-spacing:1.6px;text-transform:uppercase;white-space:nowrap}
  .brand .mark{display:block;width:7px;height:7px;background:var(--red)}
  .brand-corner{right:12px;top:20px;font-size:7.5px}
  .brand-hero{left:30px;top:32px;font-size:12px}
  .brand-hero .mark{width:11px;height:11px}

  .step{display:flex;align-items:center;gap:8px;font-size:9.2px;font-weight:500;color:var(--ink);line-height:1.1;white-space:nowrap}
  .step-icon{width:30px;height:30px;border:2px solid var(--red);border-radius:50%;display:flex;align-items:center;justify-content:center;background:var(--paper);flex:none}
  .step-icon svg{width:14px;height:14px}

  .bubble{background:var(--paper);border:2.5px solid var(--ink);border-radius:9px;font-size:7.5px;font-weight:700;line-height:1.2;padding:6px 7px;color:var(--ink);white-space:nowrap}

  .source{font-size:7.6px;color:var(--ink);line-height:1.25}
  .source small{display:block;font-size:4.6px;line-height:1.3;color:var(--ink-soft)}
  .source-list{font-size:7.6px;line-height:1.4;font-weight:500}
  .legend{display:flex;align-items:center;gap:8px;font-size:7.6px;font-weight:500}
  .legend .dot{width:14px;height:14px;border-radius:50%;display:flex;align-items:center;justify-content:center}
  .legend .dot svg{width:8px;height:8px}

  .note{font-size:6.3px;line-height:1.45;color:var(--ink-soft);width:114px;text-align:justify}
  .note.right-aligned{text-align:right}

  .stat{width:90px;height:90px;display:flex;flex-direction:column;align-items:center;justify-content:center;color:#fff;text-align:center}
  .stat b{font-family:"Roboto",sans-serif;font-weight:700;font-size:23px;line-height:1}
  .stat span{font-size:5.6px;margin-top:2px}
</style>
</head>
<body>

<!-- Page 01 : Title -->
<section class="slide slide-title" style="left:78px;top:98px">
  <div class="brand brand-hero"><span class="mark"></span>Plorven Ads</div>
  <h1 class="title" style="left:185px;top:32px">Lead Life <span class="accent">Cycle Program</span></h1>
  <p class="subtitle" style="left:185px;top:55px;font-size:9.5px">Credit Pre-Qualification and Trade-In Appraisal</p>
  <svg class="graphics" viewBox="0 0 507 285">
    <defs>
      <radialGradient id="sketchTone" cx="50%" cy="55%" r="60%">
        <stop offset="0" stop-color="#dcdcdc"/><stop offset="1" stop-color="#f3f3f3" stop-opacity="0"/>
      </radialGradient>
    </defs>
    <rect role="img" aria-label="Pencil sketch of a vintage bicycle" x="95" y="120" width="310" height="150" rx="10" fill="url(#sketchTone)"/>
    <g fill="none" stroke="var(--ink-soft)" stroke-width="0.8" stroke-dasharray="3 2">
      <path d="M58 178 Q80 140 132 126"/>
      <path d="M170 104 Q235 65 306 100"/>
      <path d="M344 110 Q395 118 405 166"/>
    </g>
    <circle cx="78" cy="199" r="19" fill="var(--red)"/>
    <path d="M67 203 h22 v-5 l-3-6 h-16 l-3 6 z M69 203 v3 M87 203 v3" fill="none" stroke="#fff" stroke-width="1.4"/>
    <circle cx="150" cy="115" r="19" fill="var(--ink)"/>
    <rect x="143" y="104" width="14" height="22" rx="2" fill="none" stroke="#fff" stroke-width="1.4"/>
    <circle cx="325" cy="104" r="19" fill="var(--red)"/>
    <rect x="314" y="97" width="22" height="15" rx="1.5" fill="none" stroke="#fff" stroke-width="1.5"/>
    <path d="M314 98 l11 8 l11 -8" fill="none" stroke="#fff" stroke-width="1.5"/>
    <circle cx="419" cy="185" r="19" fill="var(--ink)"/>
    <text x="419" y="192" text-anchor="middle" font-family="Roboto, sans-serif" font-size="20" fill="#fff">$</text>
  </svg>
  <span class="page-no">Page 01</span>
</section>

<!-- Page 04 : Trade-in valuation flow -->
<section class="slide slide-trade" style="left:614px;top:98px">
  <h2 class="title" style="left:28px;top:22px">Trade-In Leads - <span class="accent">Valuation Flow</span></h2>
  <p class="subtitle" style="left:28px;top:47px">Trade-In Leads: Offering Credit Pre-Qualification</p>
  <div class="brand brand-corner"><span class="mark"></span>Plorven Ads</div>
  <svg class="graphics" viewBox="0 0 507 285">
    <defs>
      <linearGradient id="laptopTone" x1="0" y1="0" x2="1" y2="1">
        <stop offset="0" stop-color="#e8eef3"/><stop offset=".6" stop-color="#b9c3cc"/><stop offset="1" stop-color="#d9c2ae"/>
      </linearGradient>
    </defs>
    <g stroke="var(--ink)" stroke-width="0.8" stroke-dasharray="2 2">
      <line x1="42" y1="110" x2="42" y2="138"/><line x1="42" y1="172" x2="42" y2="200"/>
    </g>
    <circle role="img" aria-label="Hands typing on a laptop showing a credit pre-qualification approval page" cx="390" cy="158" r="101" fill="url(#laptopTone)"/>
    <path d="M390 49 A109 109 0 0 0 390 267" fill="none" stroke="var(--ink)" stroke-width="7"/>
    <path d="M398 49 A109 109 0 0 1 398 267" fill="none" stroke="var(--red)" stroke-width="7"/>
    <path d="M296 131 l-6 16 l14 -15" fill="var(--paper)" stroke="var(--ink)" stroke-width="2.5" stroke-linejoin="round"/>
  </svg>
  <div class="bubble" style="left:283px;top:90px">PRE-QUALIFY<br>FOR FINANCING</div>
  <div class="step" style="left:27px;top:78px">
    <span class="step-icon"><svg viewBox="0 0 14 14"><circle cx="7" cy="4.5" r="3" fill="var(--red)"/><path d="M1.5 13 a5.5 5 0 0 1 11 0 z" fill="var(--red)"/></svg></span>Customer texts for vehicle value</div>
  <div class="step" style="left:27px;top:140px">
    <span class="step-icon"><svg viewBox="0 0 14 14"><rect x="1.5" y="2" width="11" height="8" rx="1" fill="none" stroke="var(--red)" stroke-width="1.6"/><path d="M5 13 h4 M7 10 v3" stroke="var(--red)" stroke-width="1.6"/></svg></span>Receives trade-in appraisal</div>
  <div class="step" style="left:27px;top:202px">
    <span class="step-icon"><svg viewBox="0 0 14 14"><path d="M2 12 l1-3.5 l7-7 l2.5 2.5 l-7 7 z" fill="var(--red)"/></svg></span>Offer to pre-qualify for financing appears<br>link is at the bottom of the text respons</div>
  <span class="page-no">Page 04</span>
</section>

<!-- Page 02 : Lead generation sources -->
<section class="slide slide-sources" style="left:78px;top:415px">
  <h2 class="title" style="left:28px;top:22px;line-height:1.15">Lead Generation<br><span class="accent">Sources</span></h2>
  <div class="brand brand-corner"><span class="mark"></span>Plorven Ads</div>
  <svg class="graphics" viewBox="0 0 507 285">
    <rect x="93" y="83" width="20" height="11" fill="var(--grey-light)"/>
    <polygon points="18,100 187,100 163,136 42,136" fill="var(--red)"/>
    <polygon points="42,140 163,140 139,176 66,176" fill="var(--ink)"/>
    <polygon points="66,181 139,181 117,220 88,220" fill="var(--grey)"/>
    <polygon points="94,225 110,225 110,240 120,240 102,258 84,240 94,240" fill="var(--grey-light)"/>
    <g stroke="var(--grey)" stroke-width="0.7" stroke-dasharray="2 2">
      <line x1="188" y1="118" x2="234" y2="118"/><line x1="165" y1="163" x2="234" y2="163"/><line x1="144" y1="209" x2="234" y2="209"/>
    </g>
    <g stroke="var(--grey)" stroke-width="1.3" fill="var(--paper)">
      <circle cx="175" cy="118" r="12"/><circle cx="153" cy="158" r="12"/><circle cx="132" cy="202" r="12"/>
    </g>
    <path d="M170 123 l6-6 M176 117 a3 3 0 1 1 3 -3" fill="none" stroke="var(--red)" stroke-width="1.8" stroke-linecap="round"/>
    <g fill="var(--ink)"><circle cx="149" cy="155" r="2.2"/><circle cx="157" cy="155" r="2.2"/><path d="M144 163 a5 4 0 0 1 10 0z M152 163 a5 4 0 0 1 10 0z"/></g>
    <g fill="none" stroke="var(--ink)" stroke-width="1.1"><rect x="129.5" y="195" width="5" height="4"/><path d="M132 199 v3 M127 205 v-3 h10 v3"/><rect x="125" y="205" width="4" height="3"/><rect x="130" y="205" width="4" height="3"/><rect x="135" y="205" width="4" height="3"/></g>
    <circle cx="244" cy="118" r="10" fill="var(--red)"/>
    <circle cx="244" cy="163" r="10" fill="var(--ink)"/>
    <circle cx="244" cy="209" r="10" fill="var(--grey)"/>
    <g font-family="Roboto, sans-serif" font-size="11" fill="#fff" text-anchor="middle"><text x="244" y="122">1</text><text x="244" y="167">2</text><text x="244" y="213">3</text></g>
  </svg>
  <div class="source" style="left:264px;top:93px">Pre-Qualification Tool (Fast4Loan)- How it Works<small>1. Converts Web Traffic into the highest quality lead on the market</small></div>
  <div class="source" style="left:264px;top:115px">Vorqel Email/Mail Marketing – How it Works<small>1. Delivers actionable leads from email marketing not Just OPENS<br>AND CLICKS. Show the text demo. Audiences below</small></div>
  <div class="source-list" style="left:264px;top:152px">1. Past Sold Customers (Equity Targets)<br>2. Past Service Onlu Department Customers (Conquest Sales)<br>3. Unsold Leads (from previous interactions)</div>
  <div class="source" style="left:264px;top:201px;font-weight:500">Multiple Lead Sources Feeding into the Program</div>
  <div class="legend" style="left:264px;top:224px"><span class="dot" style="background:var(--red)"><svg viewBox="0 0 8 8"><rect x=".5" y="1.5" width="7" height="5" fill="#fff"/><path d="M.5 1.5 l3.5 3 l3.5-3" fill="none" stroke="var(--red)" stroke-width=".8"/></svg></span>Envelope for email</div>
  <div class="legend" style="left:264px;top:246px"><span class="dot" style="background:var(--ink)"><svg viewBox="0 0 8 8"><circle cx="2.5" cy="3" r="1.3" fill="#fff"/><circle cx="5.5" cy="3" r="1.3" fill="#fff"/><path d="M0 7.5 a2.5 2.5 0 0 1 5 0z M3 7.5 a2.5 2.5 0 0 1 5 0z" fill="#fff"/></svg></span>A wrench for past service customers</div>
  <span class="page-no">Page 02</span>
</section>

<!-- Page 05 : Lifecycle representation -->
<section class="slide slide-lifecycle" style="left:614px;top:415px">
  <h2 class="title" style="left:28px;top:22px">Lifecycle <span class="accent">Representation</span></h2>
  <p class="subtitle" style="left:28px;top:51px">Continuous Engagement Throughout the Lead Life Cycle</p>
  <div class="brand brand-corner"><span class="mark"></span>Plorven Ads</div>
  <svg class="graphics" viewBox="0 0 507 285">
    <g fill="none" stroke-width="11">
      <path d="M203.7 110.6 A58 58 0 0 1 270 104.8" stroke="var(--blush)"/>
      <path d="M270 104.8 A58 58 0 0 1 278.3 199.4" stroke="var(--red)"/>
      <path d="M278.3 199.4 A58 58 0 0 1 190.8 184" stroke="var(--purple)"/>
      <path d="M190.8 184 A58 58 0 0 1 203.7 110.6" stroke="var(--teal)"/>
    </g>
    <g fill="none" stroke-width="0.9">
      <path d="M259 101 H274 V80 H292" stroke="var(--blush)"/>
      <path d="M318 161 H330 V176 H355" stroke="var(--red)"/>
      <path d="M241 233 V255 H216" stroke="var(--purple)"/>
      <path d="M164 161 V135 H155" stroke="var(--teal)"/>
    </g>
    <g fill="var(--paper)" stroke-width="2">
      <circle cx="241" cy="101" r="18" stroke="var(--grey-light)"/>
      <circle cx="182" cy="161" r="18" stroke="var(--teal)"/>
      <circle cx="300" cy="161" r="18" stroke="var(--red)"/>
      <circle cx="241" cy="215" r="18" stroke="var(--purple)"/>
    </g>
    <g fill="none" stroke-width="0.9">
      <circle cx="241" cy="94" r="3" stroke="var(--grey)"/>
      <path d="M179 158 l5 -5" stroke="var(--teal)"/>
      <circle cx="300" cy="154" r="3" stroke="var(--red)"/>
      <circle cx="241" cy="207" r="2" stroke="var(--purple)"/>
    </g>
    <g font-family="Roboto, sans-serif" font-size="2.8" fill="var(--ink-soft)" text-anchor="middle">
      <text x="241" y="103">Lorem ipsum</text><text x="241" y="106.5">dolor sit</text>
      <text x="182" y="163">Lorem ipsum</text><text x="182" y="166.5">dolor sit</text>
      <text x="300" y="163">Lorem ipsum</text><text x="300" y="166.5">dolor sit</text>
      <text x="241" y="217">Lorem ipsum</text><text x="241" y="220.5">dolor sit</text>
    </g>
    <rect x="212" y="146" width="7" height="7" fill="var(--red)"/>
    <text x="222" y="153" font-family="Roboto, sans-serif" font-weight="700" font-size="8" letter-spacing="1" fill="var(--ink)">PLORVEN</text>
    <text x="241" y="165" text-anchor="middle" font-family="Roboto, sans-serif" font-weight="700" font-size="6.5" letter-spacing="1.4" fill="var(--ink)">ADS</text>
  </svg>
  <p class="note" style="left:295px;top:73px">Sed ut perspiciatis unde omnis iste natus error sit voluptatem accusantium doloremque laudantium, totam rem aperiam, e quae ab illo inventore</p>
  <p class="note right-aligned" style="left:35px;top:118px">Sed ut perspiciatis unde omnis iste natus error sit voluptatem accusantium doloremque laudantium, totam rem aperiam, e quae ab illo inventore</p>
  <p class="note" style="left:360px;top:180px">Sed ut perspiciatis unde omnis iste natus error sit voluptatem accusantium doloremque laudantium, totam rem aperiam, e quae ab illo inventore</p>
  <p class="note right-aligned" style="left:100px;top:243px">Sed ut perspiciatis unde omnis iste natus error sit voluptatem accusantium doloremque laudantium, totam rem aperiam, e quae ab illo inventore</p>
  <span class="page-no">Page 05</span>
</section>

<!-- Page 03 : Credit leads flow -->
<section class="slide slide-credit" style="left:78px;top:732px">
  <h2 class="title" style="left:28px;top:22px">Credit Leads - <span class="accent">Pre-Qualified Flow</span></h2>
  <p class="subtitle" style="left:28px;top:51px">Pre-Qualified Leads: Offering Trade-In Appraisal</p>
  <div class="brand brand-corner"><span class="mark"></span>Plorven Ads</div>
  <svg class="graphics" viewBox="0 0 507 285">
    <defs>
      <linearGradient id="phoneTone" x1="0" y1="0" x2="1" y2="1">
        <stop offset="0" stop-color="#eeeeee"/><stop offset=".55" stop-color="#c9b6a4"/><stop offset="1" stop-color="#8fa4bf"/>
      </linearGradient>
    </defs>
    <g stroke="var(--ink)" stroke-width="0.8" stroke-dasharray="2 2">
      <line x1="42" y1="116" x2="42" y2="144"/><line x1="42" y1="178" x2="42" y2="207"/>
    </g>
    <circle role="img" aria-label="Hands holding a smartphone showing a dealer text conversation" cx="392" cy="158" r="101" fill="url(#phoneTone)"/>
    <path d="M390 49 A109 109 0 0 0 390 267" fill="none" stroke="var(--ink)" stroke-width="7"/>
    <path d="M398 49 A109 109 0 0 1 398 267" fill="none" stroke="var(--red)" stroke-width="7"/>
    <path d="M296 131 l-6 16 l14 -15" fill="var(--paper)" stroke="var(--ink)" stroke-width="2.5" stroke-linejoin="round"/>
  </svg>
  <div class="bubble" style="left:283px;top:90px;height:42px;display:flex;align-items:center;justify-content:center">PRE-QUALIFIED</div>
  <div class="step" style="left:27px;top:84px">
    <span class="step-icon"><svg viewBox="0 0 14 14"><rect x="1.5" y="3" width="9" height="9.5" rx="1" fill="none" stroke="var(--red)" stroke-width="1.5"/><path d="M6 8.5 l6.5-6.5" stroke="var(--red)" stroke-width="1.8"/></svg></span>Credit Leads - Pre-Qualified Flow</div>
  <div class="step" style="left:27px;top:146px">
    <span class="step-icon"><svg viewBox="0 0 14 14"><path d="M2 7.5 l3.2 3.2 l6.8-7" fill="none" stroke="var(--red)" stroke-width="2"/></svg></span>Receives credit approval</div>
  <div class="step" style="left:27px;top:209px">
    <span class="step-icon"><svg viewBox="0 0 14 14"><rect x="1" y="3" width="12" height="8.5" rx="1" fill="var(--red)"/><path d="M1 3.5 l6 4 l6-4" fill="none" stroke="#fff" stroke-width="1"/></svg></span>Email and Mail Example to<br>check trade-in value</div>
  <span class="page-no">Page 03</span>
</section>

<!-- Page 06 : Conversion goals -->
<section class="slide slide-goals" style="left:614px;top:732px">
  <div role="img" aria-label="Smiling couple receiving car keys from a dealer" style="left:0;top:0;width:400px;height:285px;background:linear-gradient(90deg,var(--photo-cool) 0%,var(--photo-warm) 40%,rgba(255,255,255,0) 100%),linear-gradient(180deg,#ffffff 0%,rgba(255,255,255,0) 35%)"></div>
  <div style="left:0;top:0;width:507px;height:70px;background:linear-gradient(180deg,rgba(255,255,255,.95) 55%,rgba(255,255,255,0))"></div>
  <h2 class="title" style="left:28px;top:22px">Lead Conversion <span class="accent">Goals</span></h2>
  <p class="subtitle" style="left:28px;top:51px">Converting Leads into Sales</p>
  <div class="brand brand-corner"><span class="mark"></span>Plorven Ads</div>
  <svg class="graphics" viewBox="0 0 507 285">
    <g fill="none" stroke="var(--grey-light)" stroke-width="4">
      <circle cx="304" cy="99" r="45"/><circle cx="406" cy="99" r="45"/><circle cx="304" cy="209" r="45"/><circle cx="406" cy="209" r="45"/>
    </g>
    <g fill="none" stroke="var(--red)" stroke-width="4">
      <path d="M304 54 A45 45 0 0 0 304 144"/>
      <path d="M406 54 A45 45 0 0 0 380 62"/>
      <path d="M304 164 A45 45 0 0 0 259 209"/>
      <path d="M406 164 A45 45 0 0 0 385 170"/>
    </g>
    <circle cx="304" cy="99" r="33" fill="var(--red)"/>
    <circle cx="406" cy="99" r="33" fill="var(--ink)"/>
    <circle cx="304" cy="209" r="33" fill="var(--ink)"/>
    <circle cx="406" cy="209" r="33" fill="var(--red)"/>
  </svg>
  <div class="stat" style="left:259px;top:54px"><b>75%</b><span>Maecenas vel tortor</span></div>
  <div class="stat" style="left:361px;top:54px"><b>9.35</b><span>Aliquam erat volutpat</span></div>
  <div class="stat" style="left:259px;top:164px"><b>12</b><span>Proin dolor</span></div>
  <div class="stat" style="left:361px;top:164px"><b>35</b><span>Curabitur venenatis</span></div>
  <span class="page-no">Page 06</span>
</section>

</body>
</html>
```